Verdanith Website Concept

We would like a one page website. Please refer to the attached files for more information.

Please reference file attachment version 1.1.

```html
<!DOCTYPE html>
<html lang="en">
<head>
<meta charset="utf-8">
<title>Verdanith — Financial Security</title>
<link href="https://fonts.googleapis.com/css2?family=Mulish:wght@400;500;600&display=swap" rel="stylesheet">
<style>
:root{
  --blue:#1b4fb5;
  --blue-dark:#1546a6;
  --ink:#2b2b2b;
  --text:#5a5a5a;
  --nav:#3a3a3a;
  --line:#dcdcdc;
  --panel:#f4f4f4;
  --field-border:#d6d6d6;
  --white:#ffffff;
}
*{box-sizing:border-box;margin:0;padding:0}
html,body{width:1115px;height:1200px;overflow:hidden}
body{position:relative;font-family:"Mulish",sans-serif;color:var(--text);background:var(--white)}
.site-header{position:absolute;left:0;top:0;width:1115px;height:94px;background:linear-gradient(#fdfdfd,#f1f1f1)}
.brand{position:absolute;left:72px;top:28px;display:flex;align-items:center;gap:10px}
.brand-mark{width:34px;height:34px;border-radius:50%;background:var(--blue)}
.brand-name{font-size:26px;font-weight:500;color:var(--blue);letter-spacing:1px}
.support{position:absolute;left:834px;top:28px;display:flex;gap:12px}
.support svg{margin-top:4px}
.support-label{font-size:14px;color:var(--ink);line-height:17px}
.support-phone{font-size:21px;color:var(--blue);line-height:26px}
.main-nav{position:absolute;left:0;top:94px;width:1115px;height:40px;background:var(--nav)}
.main-nav ul{list-style:none;display:flex;justify-content:space-between;padding:0 76px 0 76px;height:40px;align-items:center}
.main-nav a{color:var(--white);font-size:13px;text-decoration:none;font-weight:500}
.hero{position:absolute;left:69px;top:141px;width:977px;height:356px;border:4px solid #d9d9d9}
.hero-image{position:absolute;inset:0;background:linear-gradient(160deg,#f7f2c8 0%,#c9d6d6 30%,#8fa9be 70%,#7e9cb7 100%)}
.hero-image::after{content:"";position:absolute;left:340px;top:10px;width:620px;height:340px;background:radial-gradient(ellipse at 60% 55%,rgba(170,160,40,.55),rgba(170,160,40,0) 65%)}
.hero-copy{position:absolute;left:38px;top:60px;width:420px}
.hero-title{font-size:31px;font-weight:400;color:var(--ink);line-height:33px}
.hero-text{margin-top:12px;font-size:14px;line-height:21px;color:var(--white)}
.hero-btn{display:inline-block;margin-top:20px;width:116px;height:34px;line-height:34px;text-align:center;background:var(--blue);color:var(--white);font-size:16px;border-radius:2px}
.hero-dots{position:absolute;left:38px;top:318px;display:flex;gap:6px}
.hero-dots span{width:10px;height:10px;border-radius:2px;background:var(--white)}
.hero-dots span.active{background:var(--blue)}
.content{position:absolute;left:69px;top:532px;width:643px}
.section-title{font-size:21px;font-weight:400;color:var(--blue);margin-bottom:10px}
.content p{font-size:11.2px;line-height:19.7px;margin-bottom:4px}
.divider{border:0;border-top:1px solid var(--line);margin:18px 0 14px}
.services{list-style:none;margin-top:10px}
.services li{display:flex;align-items:center;gap:10px;font-size:11.2px;color:var(--blue);height:23px}
.consult{position:absolute;left:738px;top:536px;width:308px;height:547px;background:var(--panel);border:2px solid #e2e2e2}
.consult h2{position:absolute;left:18px;top:18px;font-size:20.5px;font-weight:400;color:var(--blue)}
.field{position:absolute;left:0;width:304px;display:flex;align-items:flex-start}
.field label{width:96px;text-align:right;font-size:11px;color:var(--blue);padding-top:5px}
.field .input{margin-left:20px;width:174px;height:24px;background:var(--white);border:1px solid var(--field-border)}
.field .input.area{height:83px}
.submit{position:absolute;left:197px;top:499px;width:93px;height:31px;background:#2e2e2e;color:var(--white);font-size:14px;text-align:center;line-height:31px;border-radius:2px}
.site-footer{position:absolute;left:0;top:1107px;width:1115px;height:93px;background:linear-gradient(#ececec,#f6f6f6)}
.copyright{position:absolute;left:69px;top:30px;font-size:11.5px;line-height:18px;color:var(--ink)}
.copyright span{color:var(--blue)}
.social{position:absolute;left:927px;top:33px;display:flex;gap:5px}
.social span{width:26px;height:26px;border-radius:3px}
</style>
</head>
<body>
<header class="site-header">
  <div class="brand"><span class="brand-mark"></span><span class="brand-name">Verdanith</span></div>
  <div class="support">
    <svg width="30" height="22" viewBox="0 0 30 22" aria-hidden="true"><path d="M2 8c0-4 26-4 26 0v3h-6V8H8v3H2z" fill="#555"/><rect x="5" y="11" width="20" height="10" rx="2" fill="#555"/><circle cx="15" cy="15.5" r="3" fill="#f4f4f4"/></svg>
    <div><div class="support-label">24 Hour Customer Service</div><div class="support-phone">555-014-2290</div></div>
  </div>
</header>
<nav class="main-nav">
  <ul><li><a href="#">Home</a></li><li><a href="#">About Us</a></li><li><a href="#">Our Services</a></li><li><a href="#">Request Quotes</a></li><li><a href="#">Latest News</a></li><li><a href="#">Blog</a></li><li><a href="#">Training</a></li><li><a href="#">Contact Us</a></li></ul>
</nav>
<section class="hero">
  <div class="hero-image" role="img" aria-label="Golden key with dollar sign teeth on a soft blue surface"></div>
  <div class="hero-copy">
    <h1 class="hero-title">We are a Financial Security Company.</h1>
    <p class="hero-text">Vestibulum ante ipsum primis in faucibus orci luctus et ultrices posuere cubilia. Suspendisse lobortis turpis in odio blandit ac interdum lorem euismod.</p>
    <span class="hero-btn">Read More</span>
  </div>
  <div class="hero-dots"><span class="active"></span><span></span><span></span><span></span></div>
</section>
<main class="content">
  <h2 class="section-title">About Verdanith</h2>
  <p>Verdanith is a United States-based tier one security firm specializing in the protection of financial services professionals, executives and their families.&nbsp; We manage engagements resulting from general and specific threats throughout the United States and abroad on behalf of our domestic clients.&nbsp; We deliver our services exclusively through associates and contractors with United States special operations, secret service, CIA, or equivalent experience and training.&nbsp; We are one of only a handful of domestic security firms that offers scalable, tier one security services in every market in the United States.</p>
  <p>If you have a general or specific threat you would like to have assessed, it will be our privilege to evaluate your circumstances and provide you with an opinion of how to best address your security needs.&nbsp; Not all security circumstances require tier one professionals.&nbsp; It will be our pleasure to direct you to other firms in your market if you or we believe our service levels are not warranted.</p>
  <p>Our firm was created as the result of a specific threat to two of our founders resulting from a private equity transaction with a hostile seller.&nbsp; If you are a transaction professional or executive who is experiencing the fear and&nbsp; uncertainty of the risks associated with a general or specific security threat, it will be our privilege to help you manage this challenging process.</p>
  <hr class="divider">
  <h2 class="section-title">Service Offerings</h2>
  <p>Aliquam molestie, mi et imperdiet euismod, dui purus auctor tellus, et interdum lacus lectus et ante. Sed accumsan sollicitudin sapien, sit amet adipiscing turpis gravida ac.</p>
  <ul class="services">
    <li><svg width="10" height="9" viewBox="0 0 10 9" aria-hidden="true"><path d="M1 5l3 3 5-7" stroke="#333" stroke-width="2" fill="none"/></svg>Threat Assessment</li>
    <li><svg width="10" height="9" viewBox="0 0 10 9" aria-hidden="true"><path d="M1 5l3 3 5-7" stroke="#333" stroke-width="2" fill="none"/></svg>Threat Avoidance Plan &amp; Dossier Creation</li>
    <li><svg width="10" height="9" viewBox="0 0 10 9" aria-hidden="true"><path d="M1 5l3 3 5-7" stroke="#333" stroke-width="2" fill="none"/></svg>Elite Executive Protection</li>
    <li><svg width="10" height="9" viewBox="0 0 10 9" aria-hidden="true"><path d="M1 5l3 3 5-7" stroke="#333" stroke-width="2" fill="none"/></svg>Threat Avoidance Plan &amp; Dossier Maintenance</li>
  </ul>
</main>
<aside class="consult">
  <h2>Request for Consultation</h2>
  <div class="field" style="top:56px"><label>First Name</label><span class="input"></span></div>
  <div class="field" style="top:88px"><label>Last Name</label><span class="input"></span></div>
  <div class="field" style="top:120px"><label>Home Phone</label><span class="input"></span></div>
  <div class="field" style="top:151px"><label>Work Phone</label><span class="input"></span></div>
  <div class="field" style="top:183px"><label>Cell Phone</label><span class="input"></span></div>
  <div class="field" style="top:215px"><label>Email Address</label><span class="input"></span></div>
  <div class="field" style="top:247px"><label>Address</label><span class="input"></span></div>
  <div class="field" style="top:279px"><label>Address</label><span class="input"></span></div>
  <div class="field" style="top:310px"><label>City</label><span class="input"></span></div>
  <div class="field" style="top:342px"><label>State</label><span class="input"></span></div>
  <div class="field" style="top:374px"><label>Zip</label><span class="input"></span></div>
  <div class="field" style="top:406px"><label>Message</label><span class="input area"></span></div>
  <span class="submit">Submit</span>
</aside>
<footer class="site-footer">
  <div class="copyright">Copyright © 2014. <span>Verdanith.</span><br>All Right Reserved</div>
  <div class="social">
    <span style="background:#3b5a9a"></span><span style="background:#4fb8e3"></span><span style="background:#ef8a22"></span><span style="background:#1f7bb6"></span>
  </div>
</footer>
</body>
</html>
```